Business Card Design Project

Business Card
We are rebranding with a new logo
Industry/Entity Type
Business
Contact Information for Business Card
Dennis Morvale +61 487215963 dennis@quorv.com.au P.O. Box 872 Fernlow QLD 4309
Requirements
Must have
- Logo

```html
<!DOCTYPE html>
<html lang="en">
<head>
<meta charset="utf-8">
<title>Quorv International – Business Card</title>
<link rel="stylesheet" href="https://fonts.googleapis.com/css2?family=Great+Vibes&family=Roboto:wght@400;500&display=swap">
<style>
  :root {
    --page-bg: #e6e7e8;
    --card-bg-top: #f7f8f8;
    --card-bg-bottom: #eceeef;
    --teal-deep: #0b5d74;
    --teal-light: #17819c;
    --ink-teal: #174f60;
    --ink-dark: #222a2e;
    --contact-ink: #f6b47a;
    --icon-orange: #e8762b;
  }
  html, body {
    margin: 0;
    width: 1200px;
    height: 1010px;
    overflow: hidden;
    background: var(--page-bg);
  }
  .business-card {
    position: absolute;
    left: 75px;
    top: 201px;
    width: 1050px;
    height: 608px;
    background: linear-gradient(180deg, var(--card-bg-top), var(--card-bg-bottom));
    box-shadow: 0 10px 30px rgba(0,0,0,0.15);
    overflow: hidden;
    font-family: "Roboto", Arial, sans-serif;
  }
  .lower-band {
    position: absolute;
    left: 0;
    right: 0;
    bottom: 0;
    height: 200px;
    background: linear-gradient(100deg, var(--teal-light), var(--teal-deep));
  }
  .brand-name {
    position: absolute;
    left: 112px;
    top: 240px;
    margin: 0;
    font-family: "Roboto", Arial, sans-serif;
    font-weight: 500;
    font-size: 46px;
    line-height: 1.1;
    letter-spacing: 1px;
    color: var(--teal-deep);
  }
  .holder {
    position: absolute;
    right: 48px;
    top: 82px;
    text-align: right;
  }
  .holder-name {
    margin: 0;
    font-family: "Great Vibes", cursive;
    font-weight: 400;
    font-size: 58px;
    line-height: 1;
    color: var(--ink-teal);
  }
  .holder-title {
    margin: 10px 0 0;
    font-size: 23px;
    color: var(--ink-dark);
  }
  .contact-list {
    position: absolute;
    right: 40px;
    top: 464px;
    margin: 0;
    padding: 0;
    list-style: none;
    text-align: right;
  }
  .contact-item {
    display: flex;
    justify-content: flex-end;
    align-items: center;
    gap: 18px;
    height: 35px;
    font-size: 23px;
    color: var(--contact-ink);
    letter-spacing: 0.3px;
  }
  .contact-icon {
    width: 22px;
    height: 22px;
    flex: none;
  }
</style>
</head>
<body>
  <main class="business-card">
    <div class="lower-band" role="img" aria-label="Decorative teal and orange wave band along the lower edge of the card"></div>

    <p class="brand-name">QUORV<br>INTERNATIONAL</p>

    <section class="holder">
      <h1 class="holder-name">Dennis Morvale</h1>
      <p class="holder-title">Managing Director</p>
    </section>

    <ul class="contact-list">
      <li class="contact-item">
        <span>+61 487215963</span>
        <svg class="contact-icon" viewBox="0 0 24 24" aria-hidden="true">
          <path d="M3 9c0-3 4-5 9-5s9 2 9 5l-4 1-1-3H8L7 10 3 9Z M6 12h12l2 8H4l2-8Z" fill="var(--icon-orange)"/>
        </svg>
      </li>
      <li class="contact-item">
        <span>dennis@quorv.com.au</span>
        <svg class="contact-icon" viewBox="0 0 24 24" aria-hidden="true">
          <rect x="2" y="5" width="20" height="14" fill="var(--icon-orange)"/>
          <path d="M2 5l10 8 10-8" fill="none" stroke="var(--teal-deep)" stroke-width="1.6"/>
        </svg>
      </li>
      <li class="contact-item">
        <span>P.O. Box 872 Fernlow QLD 4309</span>
        <svg class="contact-icon" viewBox="0 0 24 24" aria-hidden="true">
          <path d="M12 2a7 7 0 0 0-7 7c0 5 7 13 7 13s7-8 7-13a7 7 0 0 0-7-7Z" fill="var(--icon-orange)"/>
          <circle cx="12" cy="9" r="2.6" fill="var(--teal-deep)"/>
        </svg>
      </li>
    </ul>
  </main>
</body>
</html>
```